Brookvane Consulting Business Card Design

Business Card Design for Brookvane Consulting. Brookvane Consulting is a boutique consultancy based in Atlanta, GA., that specializes in marketing strategy, organization planning, and leadership development. We provide solutions for small businesses and startups as well as Vantage 300 companies.

http://brookvaneconsulting.com/

Target Market(s)

We provide solutions for small businesses and startups as well as Vantage 300 companies.

Industry/Entity Type

Consulting

Contact Information for Business Card

Two sided business card with priority on contact information, logo, tag line (Guidance to Plan Ahead, Act Boldly, Grow Further)

Colors

Designer to choose colors to be used in the design.

Requirements
Must have
• contact information, logo, tag line (Guidance to Plan Ahead, Act Boldly, Grow Further)
• Simple no over communication.
Nice to have
• I would like to see different placements of logo and creative use of both sides of the card
Should not have
• Do not put too much information on the card.

```html
<!DOCTYPE html>
<html lang="en">
<head>
<meta charset="utf-8">
<title>Brookvane Consulting Business Card</title>
<link rel="stylesheet" href="https://fonts.googleapis.com/css2?family=Lato:wght@400;700&family=Roboto:wght@400&display=swap">
<style>
  :root {
    --backdrop: #9b6a46;
    --card-front: #1e2022;
    --card-back: #222426;
    --card-back-pattern: #27292b;
    --ink-white: #ffffff;
    --ink-soft: #e4e4e4;
    --ink-grey: #a9a9a9;
  }
  * { margin: 0; padding: 0; box-sizing: border-box; }
  html, body {
    width: 1200px;
    height: 960px;
    overflow: hidden;
  }
  body {
    position: relative;
    background: var(--backdrop);
    font-family: "Lato", Arial, sans-serif;
  }
  .card {
    position: absolute;
    width: 600px;
    height: 344px;
    box-shadow: 0 3px 10px rgba(0, 0, 0, 0.35);
    color: var(--ink-white);
    text-align: center;
  }
  .card--front {
    left: 322px;
    top: 106px;
    background: var(--card-front);
  }
  .card--back {
    left: 320px;
    top: 493px;
    background: var(--card-back);
    overflow: hidden;
  }
  .card__pattern {
    position: absolute;
    inset: 0;
    background: linear-gradient(180deg, var(--card-back-pattern), var(--card-back));
  }
  .wordmark {
    position: absolute;
    left: 0;
    right: 0;
    display: flex;
    justify-content: center;
    align-items: center;
    gap: 12px;
    font-family: "Lato", Arial, sans-serif;
    font-weight: 400;
    font-size: 34px;
    letter-spacing: 1px;
    color: var(--ink-white);
  }
  .wordmark__square {
    width: 18px;
    height: 18px;
    background: var(--ink-white);
  }
  .card--front .wordmark { top: 142px; }
  .card--back .wordmark { top: 100px; }
  .tagline {
    position: absolute;
    left: 0;
    right: 0;
    top: 282px;
    font-family: "Roboto", Arial, sans-serif;
    font-size: 14.5px;
    color: var(--ink-soft);
  }
  .contact {
    position: absolute;
    left: 0;
    right: 0;
    top: 188px;
  }
  .contact__name {
    font-weight: 700;
    font-size: 19px;
    letter-spacing: 0.5px;
    color: var(--ink-grey);
    text-transform: uppercase;
    line-height: 24px;
  }
  .contact__role {
    font-weight: 700;
    font-size: 15px;
    color: var(--ink-soft);
    line-height: 22px;
  }
  .contact__lines {
    margin-top: 10px;
    font-size: 14px;
    color: var(--ink-soft);
    line-height: 20px;
  }
  .contact__web { letter-spacing: 1.5px; }
</style>
</head>
<body>
  <section class="card card--front">
    <div class="wordmark">
      <span class="wordmark__square"></span>
      <span class="wordmark__name">Brookvane Consulting</span>
    </div>
    <p class="tagline">Guidance to Plan Ahead, Act Boldly, Grow Further</p>
  </section>

  <section class="card card--back">
    <div class="card__pattern" role="img" aria-label="Faint tonal geometric pattern covering the card back"></div>
    <div class="wordmark">
      <span class="wordmark__square"></span>
      <span class="wordmark__name">Brookvane Consulting</span>
    </div>
    <div class="contact">
      <p class="contact__name">Darius Whitfield</p>
      <p class="contact__role">Founder/Managing Director</p>
      <div class="contact__lines">
        <p>P. 555-014-2290 E. darius@brookvaneconsulting.com</p>
        <p class="contact__web">www.brookvaneconsulting.com</p>
      </div>
    </div>
  </section>
</body>
</html>
```